Business Card: RW Office Partners - Your organised problem solver

Business Name: RW Office Partners
Website: www.rwofficepartners.com.au
Email: marisol@rwofficepartners.com.au
Mobile: 61 482 907 236
Facebook: @rwofficepartners
Instrgram: @rwofficepartners

Brading Colours:
HEX
#986474
#ddccd3
#7a8498
#c9d8e4
#000000
#ffffff

Tag Line: Your dependable desk partner

Link to DRAFT website:
https://deskhelpcollective.wixsite.com/rw-office-partners

About Page from the website:
My name is Marisol Wrenfield, and I would love to assist you to become more productive in your day to day and achieve your business and personal goals.
My mission is to give you time, time to work on the important tasks of your business or to be able to spend more time with your family. I will take on the tasks you don’t have time for, don’t know well or simply don’t like to do.
I have an extensive background in Administration, Tender Coordination, Document Control, WHS and Quality Management working primarily in the Construction, Mining and Corporate World.
I am passionate about being organised, having order and making things in your life (and mine) easier! I love to watch something unfold and grow into something amazing! I am known for being the go-to problem solver, the organiser of all things, producing high standards of work even under pressure. I’m also a confident communicator, and I understand that you’re busy running your business.

Target Market(s)

Small to Medium Business who require assistance in their business by a virtual assistant.

Industry/Entity Type

Virtual Assistant

Contact Information for Business Card

Mobile: 61 482 907 236

Font styles to use
Sans Serif

Colors
ffffff

Requirements
Must have
• Branding Colours as outlined.
Contact Details as outlined.
Logo as provided.
Proper contact details - mobile, facebook, instragm, website.
Simple, Elegant, very clean looking.
Should not have
• Note cute with pictures.
Not too girly as still want to market to construction companies.

```html
<!DOCTYPE html>
<html lang="en">
<head>
<meta charset="utf-8">
<title>RW Office Partners – Business Card</title>
<link href="https://fonts.googleapis.com/css2?family=Montserrat:wght@500;600&family=Roboto:wght@400&display=swap" rel="stylesheet">
<style>
  :root {
    --plum: #986474;
    --plum-light: #ddccd3;
    --slate: #7a8498;
    --slate-light: #c9d8e4;
    --ink: #2f2f33;
    --paper: #ffffff;
    --backdrop: #e9e7e8;
  }
  * { margin: 0; padding: 0; box-sizing: border-box; }
  html, body {
    width: 1200px; height: 1200px; overflow: hidden;
    background: var(--backdrop);
  }
  .canvas { position: relative; width: 1200px; height: 1200px; }
  .card {
    position: absolute;
    width: 712px;
    background: var(--paper);
    border-radius: 24px;
    overflow: hidden;
    box-shadow: 0 2px 6px rgba(0,0,0,0.08);
  }
  .card--front { left: 238px; top: 118px; height: 419px; }
  .card--back  { left: 230px; top: 645px; height: 417px; }

  .brand {
    position: absolute;
    display: flex; align-items: center; gap: 18px;
    font-family: "Montserrat", sans-serif;
    font-weight: 600;
    color: var(--slate);
    white-space: nowrap;
  }
  .brand__mark { background: var(--plum); flex: none; }
  .brand__name { display: block; }
  .brand__line { display: block; }
  .card--front .brand {
    left: 0; right: 0; justify-content: center;
    top: 134px; font-size: 54px; line-height: 56px;
  }
  .card--front .brand__mark { width: 30px; height: 30px; }
  .card--back .brand {
    right: 27px; top: 46px; font-size: 38px; line-height: 40px; gap: 14px;
  }
  .card--back .brand__mark { width: 22px; height: 22px; }

  .tagline {
    position: absolute; right: 27px; top: 131px;
    font-family: "Montserrat", sans-serif; font-weight: 600;
    font-size: 16.5px; letter-spacing: 2.2px; color: var(--ink);
    text-transform: uppercase;
  }

  .socials {
    position: absolute; font-family: "Roboto", sans-serif;
    font-size: 18px; color: var(--ink);
  }
  .socials__item { display: flex; align-items: center; gap: 10px; }
  .socials__dot {
    width: 15px; height: 15px; border-radius: 3px; background: var(--plum); flex: none;
  }
  .card--front .socials {
    left: 0; right: 0; top: 352px;
    display: flex; justify-content: center; gap: 20px;
  }
  .card--back .socials {
    right: 27px; top: 333px;
    display: flex; flex-direction: column; gap: 5px; align-items: flex-start;
  }

  .accent-band {
    position: absolute; left: 0; right: 0; bottom: 0; height: 15px; display: flex;
  }
  .accent-band__plum { flex: 1; background: var(--plum); }
  .accent-band__slate { flex: 1; background: var(--slate); }

  .person {
    position: absolute; left: 29px; right: 27px; top: 220px;
    font-family: "Roboto", sans-serif;
  }
  .person__name {
    font-family: "Montserrat", sans-serif; font-weight: 600;
    font-size: 27px; color: var(--plum); line-height: 34px;
  }
  .person__role {
    display: flex; align-items: center; gap: 14px;
    font-size: 18px; color: var(--ink); margin-top: 2px;
  }
  .person__rule { flex: 1; height: 1.5px; background: var(--slate); }

  .contacts {
    position: absolute; left: 29px; top: 307px;
    font-family: "Roboto", sans-serif; font-size: 18px; color: var(--ink);
    display: flex; flex-direction: column; gap: 5px;
  }
  .contacts__item { display: flex; align-items: center; gap: 13px; line-height: 22px; }
  .contacts__icon { width: 18px; height: 16px; flex: none; }
</style>
</head>
<body>
<main class="canvas">

  <section class="card card--front" aria-label="Card front">
    <div class="brand">
      <span class="brand__mark"></span>
      <span class="brand__name"><span class="brand__line">RW Office</span><span class="brand__line">Partners</span></span>
    </div>
    <div class="socials">
      <span class="socials__item"><span class="socials__dot"></span>@rwofficepartners</span>
      <span class="socials__item"><span class="socials__dot"></span>@rwofficepartners</span>
    </div>
    <div class="accent-band">
      <span class="accent-band__plum"></span>
      <span class="accent-band__slate"></span>
    </div>
  </section>

  <section class="card card--back" aria-label="Card back">
    <div class="brand">
      <span class="brand__mark"></span>
      <span class="brand__name"><span class="brand__line">RW Office</span><span class="brand__line">Partners</span></span>
    </div>
    <p class="tagline">Your dependable desk partner</p>

    <div class="person">
      <p class="person__name">Marisol Wrenfield</p>
      <p class="person__role">Virtual Assistant <span class="person__rule"></span></p>
    </div>

    <div class="contacts">
      <p class="contacts__item">
        <svg class="contacts__icon" viewBox="0 0 18 16" aria-hidden="true">
          <path d="M2 6 Q9 0 16 6 L14 8 L12 5 L6 5 L4 8 Z" fill="#555"/>
          <rect x="4" y="8" width="10" height="6" rx="1" fill="#555"/>
          <circle cx="9" cy="11" r="1.6" fill="#fff"/>
        </svg>
        61 482 907 236
      </p>
      <p class="contacts__item">
        <svg class="contacts__icon" viewBox="0 0 18 16" aria-hidden="true">
          <rect x="1" y="3" width="16" height="11" fill="#555"/>
          <path d="M1.5 3.5 L9 9.5 L16.5 3.5" stroke="#fff" stroke-width="1.4" fill="none"/>
        </svg>
        marisol@rwofficepartners.com.au
      </p>
      <p class="contacts__item">
        <svg class="contacts__icon" viewBox="0 0 18 16" aria-hidden="true">
          <g fill="none" stroke="#666" stroke-width="1.2">
            <circle cx="9" cy="8" r="6.5"/>
            <ellipse cx="9" cy="8" rx="2.8" ry="6.5"/>
            <path d="M2.5 8 H15.5 M3.5 4.8 H14.5 M3.5 11.2 H14.5"/>
          </g>
        </svg>
        www.rwofficepartners.com.au
      </p>
    </div>

    <div class="socials">
      <span class="socials__item"><span class="socials__dot"></span>@rwofficepartners</span>
      <span class="socials__item"><span class="socials__dot"></span>@rwofficepartners</span>
    </div>
  </section>

</main>
</body>
</html>
```